Redgum Ridge Towing website

We need a website design for a towing company based in Australia.
The design should be simple and minimalist. The site can be in colours of the logo are Blue, Red and White (see attached) - but we'd like to see options in some sort of industrial looking metallic theme if possible.
We base our business on our friendly and efficient customer service, the design should attempt to convey this in some way.

```html
<!DOCTYPE html>
<html lang="en">
<head>
<meta charset="utf-8">
<title>Redgum Ridge Towing</title>
<link href="https://fonts.googleapis.com/css2?family=Exo:wght@400;500&family=Open+Sans:wght@400;600&display=swap" rel="stylesheet">
<style>
:root{
  --blue:#2f86e8;
  --blue-dark:#1f63b8;
  --blue-light:#5aa6f5;
  --ink:#111;
  --text:#444;
  --muted:#8a8a8a;
  --page:#f6f5f6;
  --field:#e6e5e6;
  --footer:#1c1c1c;
}
*{margin:0;padding:0;box-sizing:border-box}
html,body{width:961px;height:1200px;overflow:hidden;background:var(--page)}
body{position:relative;font-family:"Open Sans",sans-serif;color:var(--text)}
.abs{position:absolute}

.site-header{left:0;top:0;width:961px;height:106px;background:linear-gradient(#f4f4f4,#e9e9e9)}
.brand{left:150px;top:38px;display:flex;align-items:center;gap:8px}
.brand-mark{width:16px;height:16px;background:var(--blue-dark)}
.brand-name{font-family:"Exo",sans-serif;font-weight:500;font-size:15px;color:var(--blue-dark)}
.phone{left:726px;top:13px;display:flex;align-items:center;gap:8px;font-size:12px;color:#555}
.phone svg{width:14px;height:14px}
.search{left:649px;top:54px;width:166px;height:29px;border:1px solid #dcdcdc;border-radius:5px;background:#f7f7f7}
.search-field{position:absolute;left:4px;top:3px;width:136px;height:22px;border-radius:4px;background:linear-gradient(var(--blue-light),var(--blue));color:#fff;font-size:8px;font-weight:600;padding:6px 7px}
.search svg{position:absolute;right:8px;top:7px;width:14px;height:14px}

.main-nav{left:0;top:106px;width:961px;height:39px;background:linear-gradient(var(--blue-light),var(--blue) 60%,#2a7adb)}
.main-nav ul{list-style:none;position:absolute;left:138px;top:0;display:flex;height:39px}
.main-nav li{font-family:"Exo",sans-serif;font-size:11.5px;color:#0d2340;letter-spacing:.4px;line-height:39px;padding:0 12px 0 12px;margin-right:4px}
.main-nav li.active{background:var(--blue-dark);color:#fff}

.hero{left:0;top:145px;width:961px;height:401px;background:linear-gradient(100deg,#2b2b2b 0%,#6d6d6d 35%,#9e9e9e 55%,#8a2a3a 75%,#7a1c2c 100%)}
.hero-caption{left:145px;top:361px;width:383px;height:92px;background:rgba(20,20,20,.72);color:#fff;font-family:"Exo",sans-serif;padding:14px 13px;white-space:nowrap}
.hero-caption .l1{font-size:23px;letter-spacing:.5px}
.hero-caption .l2{font-size:18.5px;margin-top:12px;letter-spacing:.6px}
.hero-arrow{top:332px;width:28px;height:28px;border-radius:50%;background:#222}
.hero-arrow svg{width:28px;height:28px}
.dots{left:422px;top:510px;display:flex;gap:8px}
.dots span{width:12px;height:12px;border-radius:50%;background:#e6e6e6}
.dots span.on{background:var(--blue-dark)}

.features{left:0;top:546px;width:961px;height:148px;background:linear-gradient(#ececec,#c8c8c8)}
.feature{top:20px;width:210px;text-align:center}
.feature svg{height:38px}
.feature h3{font-family:"Exo",sans-serif;font-weight:500;font-size:12px;color:#111;margin-top:5px;white-space:nowrap}
.feature p{font-size:8.5px;line-height:12.3px;color:#444;margin-top:5px}

.welcome h2{left:145px;top:715px;font-family:"Exo",sans-serif;font-weight:500;font-size:12px;color:#111;white-space:nowrap}
.welcome-text{left:150px;top:744px;font-size:10.2px;line-height:20.5px;color:#555;white-space:nowrap}

.quick{left:594px;top:718px;width:214px;height:190px;background:linear-gradient(90deg,#efefef,var(--page) 40%)}
.quick h2{position:absolute;left:8px;top:12px;display:flex;align-items:center;gap:6px;font-family:"Exo",sans-serif;font-weight:500;font-size:11.5px;color:#111;white-space:nowrap}
.quick h2 svg{width:24px;height:15px}
.field{position:absolute;left:16px;width:199px;background:var(--field);border-radius:2px;color:#c3c3c3;font-size:11px;padding:6px 11px;white-space:nowrap}
.send{left:744px;top:898px;width:64px;height:24px;border-radius:2px;background:linear-gradient(var(--blue-light),var(--blue-dark));color:#fff;font-family:"Exo",sans-serif;font-size:11px;text-align:center;line-height:24px;letter-spacing:.5px}

.divider{left:260px;top:966px;width:396px;height:1px;background:linear-gradient(90deg,transparent,#d5d5d5,transparent)}

.gallery h2{left:144px;top:995px;font-family:"Exo",sans-serif;font-weight:500;font-size:11.5px;color:#111}
.g-btn{top:988px;width:25px;height:20px;border-radius:2px}
.g-btn.prev{left:758px;background:linear-gradient(#f4f4f4,#d4d4d4);border:1px solid #bbb}
.g-btn.next{left:791px;background:linear-gradient(var(--blue-light),var(--blue-dark))}
.g-btn svg{width:23px;height:18px}
.g-rule{left:144px;top:1017px;width:672px;height:1px;background:#d8d8d8}
.thumbs{left:146px;top:1030px;display:flex;gap:6px}
.thumb{width:129px;height:84px;background:#fff;border:1px solid #ddd;padding:2px}
.thumb div{width:100%;height:100%}

.site-footer{left:0;top:1141px;width:961px;height:59px;background:var(--footer);border-top:3px solid var(--blue-dark)}
.foot-links{position:absolute;left:145px;top:14px;font-size:7.5px;color:#ccc;white-space:nowrap}
.copy{position:absolute;left:145px;top:36px;font-size:7px;color:#888;white-space:nowrap}
.social{position:absolute;left:617px;top:12px;display:flex;gap:7px}
.social span{width:28px;height:28px;border-radius:4px;background:linear-gradient(#e4e4e4,#a9a9a9)}
</style>
</head>
<body>

<header class="site-header abs">
  <div class="brand abs"><span class="brand-mark"></span><span class="brand-name">Redgum Ridge Towing</span></div>
  <div class="phone abs">
    <svg viewBox="0 0 14 14"><rect x="0.5" y="0.5" width="13" height="13" rx="2" fill="#ddd" stroke="#999"/><path d="M4 3.5l1.6 0 .6 2-1 .8c.5 1 1.3 1.8 2.3 2.3l.8-1 2 .6 0 1.6c-3.5.3-6.6-2.8-6.3-6.3z" fill="#333"/></svg>
    <span>555 014 927</span>
  </div>
  <div class="search abs">
    <div class="search-field">SEARCH</div>
    <svg viewBox="0 0 14 14"><circle cx="5.5" cy="5.5" r="4" fill="none" stroke="#777" stroke-width="1.6"/><path d="M8.5 8.5l4 4" stroke="#777" stroke-width="2"/></svg>
  </div>
</header>

<nav class="main-nav abs">
  <ul>
    <li class="active">HOME</li><li>ABOUT US</li><li>SERVICES</li><li>GALLERY</li><li>NEWS &amp; EVENTS</li><li>CONTACT US</li><li>BLOG</li>
  </ul>
</nav>

<section class="hero abs" role="img" aria-label="Tow truck lifting a red car, motion-blurred street scene"></section>
<div class="hero-caption abs">
  <div class="l1">24/7 TOWING AND RECOVERY</div>
  <div class="l2">FROM LIGHT TO EXTREME HEAVY DUTY</div>
</div>
<div class="hero-arrow abs" style="left:12px"><svg viewBox="0 0 28 28"><path d="M16 8l-6 6 6 6" fill="none" stroke="#fff" stroke-width="2.5"/></svg></div>
<div class="hero-arrow abs" style="left:918px"><svg viewBox="0 0 28 28"><path d="M12 8l6 6-6 6" fill="none" stroke="#fff" stroke-width="2.5"/></svg></div>
<div class="dots abs"><span></span><span></span><span class="on"></span><span></span><span></span><span></span></div>

<section class="features abs">
  <div class="feature abs" style="left:149px">
    <svg viewBox="0 0 70 38"><path d="M2 10h66v4H2z M14 14l6-10h30l6 10z M4 16h62v14H4z" fill="#111"/><rect x="20" y="7" width="30" height="6" fill="#ececec"/><rect x="8" y="20" width="10" height="4" fill="#ececec"/><rect x="52" y="20" width="10" height="4" fill="#ececec"/><rect x="22" y="21" width="26" height="2" fill="#ececec"/><rect x="6" y="30" width="10" height="7" fill="#111"/><rect x="54" y="30" width="10" height="7" fill="#111"/></svg>
    <h3>Auto Towing Services</h3>
    <p>Lorem ipsum dolor sit amet, consectetur adipiscing elit. Aliquam ultricies magna non lectus elementum consectetur.</p>
  </div>
  <div class="feature abs" style="left:375px">
    <svg viewBox="0 0 40 40"><rect x="17" y="0" width="6" height="40" fill="#111"/><path d="M6 5h28l5 4-5 4H6z M2 15h30v8H2l-3-4z M8 25h28l4 4-4 4H8z" fill="#111"/></svg>
    <h3>Road Side Assitance</h3>
    <p>Lorem ipsum dolor sit amet, consectetur adipiscing elit. Aliquam ultricies magna non lectus elementum consectetur.</p>
  </div>
  <div class="feature abs" style="left:599px">
    <svg viewBox="0 0 52 38"><rect x="12" y="4" width="28" height="14" rx="3" fill="#111"/><rect x="0" y="16" width="52" height="4" fill="#111"/><rect x="0" y="20" width="10" height="12" fill="#111"/><rect x="20" y="20" width="12" height="12" fill="#111"/><rect x="42" y="20" width="10" height="12" fill="#111"/><rect x="0" y="30" width="52" height="4" fill="#111"/></svg>
    <h3>Emergency Services</h3>
    <p>Lorem ipsum dolor sit amet, consectetur adipiscing elit. Aliquam ultricies magna non lectus elementum consectetur.</p>
  </div>
</section>

<section class="welcome">
  <h2 class="abs">Welcome To Our Towing Company</h2>
  <p class="welcome-text abs">Proin lacinia metus non est interdum cursus pellentesque massa facilisis. Nulla hendrerit<br>sem in mauris aliquet posuere. Nunc felis lectus, placerat vitae suscipit a, pellentesque eu<br>velit. Proin accumsan venenatis congue. Sed ac purus vitae orci dictum tincidunt sit amet<br>vitae leo. Aenean sed ante eu urna mollis volutpat non nec augue. Nunc eleifend viverra<br>purus sed molestie. Donec volutpat, lorem vitae condimentum faucibus, neque justo moles-<br>tie dui, eget gravida velit dolor nec nisl. Duis malesuada pulvinar vehicula. Nulla urna massa,<br>varius in luctus ultricies, fermentum nec orci.<br>lorem vitae condimentum faucibus, neque justo molestie dui, eget gravida velit dolor nec<br>nisl. Duis malesuada pulvinar vehicula. Nulla urna massa, varius in luctus ultricies, fermen-<br>tum nec orci.</p>
</section>

<aside class="quick abs">
  <h2><svg viewBox="0 0 24 15"><rect width="24" height="15" fill="#111"/><path d="M1 1l11 8 11-8" fill="none" stroke="#fff" stroke-width="1.5"/></svg>Quick Contact</h2>
  <div class="field" style="top:45px;height:26px">Your Name</div>
  <div class="field" style="top:81px;height:26px">Your Mail Address</div>
  <div class="field" style="top:116px;height:54px">Your Message</div>
</aside>
<div class="send abs">SEND</div>

<div class="divider abs"></div>

<section class="gallery">
  <h2 class="abs">Our Gallery</h2>
  <div class="g-btn prev abs"><svg viewBox="0 0 23 18"><path d="M13 5l-4 4 4 4" fill="none" stroke="#222" stroke-width="2"/></svg></div>
  <div class="g-btn next abs"><svg viewBox="0 0 25 20"><path d="M11 6l4 4-4 4" fill="none" stroke="#fff" stroke-width="2"/></svg></div>
  <div class="g-rule abs"></div>
  <div class="thumbs abs">
    <div class="thumb"><div role="img" aria-label="Red flatbed tow truck carrying a pickup" style="background:linear-gradient(#8a8f96,#b23a3a 60%,#5a5a5a)"></div></div>
    <div class="thumb"><div role="img" aria-label="Heavy wrecker tow truck on a street" style="background:linear-gradient(#c9ccd0,#6f6a5e 55%,#8f8f8f)"></div></div>
    <div class="thumb"><div role="img" aria-label="Flatbed truck with a purple car" style="background:linear-gradient(#4d7a3e,#4a4a6a 55%,#9a9a9a)"></div></div>
    <div class="thumb"><div role="img" aria-label="Dark blue tow truck in a parking lot" style="background:linear-gradient(#3f6e3a,#1f2a44 55%,#8a8a8a)"></div></div>
    <div class="thumb"><div role="img" aria-label="Tow truck loading a yellow motorcycle" style="background:linear-gradient(#a9b0b5,#3a3a3a 55%,#6f7f4a)"></div></div>
  </div>
</section>

<footer class="site-footer abs">
  <div class="foot-links">Sitemap&nbsp; | &nbsp;Privacy Policy&nbsp; | &nbsp;Terms Of Use</div>
  <div class="copy">Copyright 2014. All right reserved.</div>
  <div class="social"><span></span><span></span><span></span><span></span><span></span><span></span></div>
</footer>

</body>
</html>
```